Update patient consent forms and contract

Objective
Redesign the existing patient contract information document to create a modern,contempory, and easy-to-understand experience for patients. The updated design should improve readability, accessibility, and overall presentation while maintaining compliance with healthcare and legal requirements.

Key Deliverables

Refreshed visual design and layout
Improved information hierarchy and readability
Modern typography and colour palette aligned with brand guidelines
Clear section headings and navigation
Print-ready and digital versions (PDF)

Include KEV Logo within patient KEV consent to treatment. Ideally this document should be portrait not landscape.
Updates

I would love a front page to be included in the document

```html
<!DOCTYPE html>
<html lang="en">
<head>
<meta charset="utf-8">
<title>Orthodontic Treatment Consent – Document Pages</title>
<link href="https://fonts.googleapis.com/css2?family=Poppins:wght@300;400;500;600;700&display=swap" rel="stylesheet">
<style>
:root{
  --bg:#8b8b8b;
  --paper:#ffffff;
  --blue:#1a9ad6;
  --ink:#2a2a2a;
  --body:#444444;
  --muted:#7a7a7a;
  --rule:#cfcfcf;
}
*{box-sizing:border-box;margin:0;padding:0}
html,body{width:1200px;height:993px;overflow:hidden}
body{background:var(--bg);font-family:"Poppins",sans-serif;color:var(--body);position:relative}
.page{position:absolute;width:314px;height:407px;background:var(--paper);overflow:hidden}
.p1{left:115px;top:83px}.p2{left:443px;top:83px}.p3{left:770px;top:83px}
.p4{left:115px;top:503px}.p5{left:443px;top:503px}.p6{left:770px;top:503px}
.abs{position:absolute}

.brand{display:flex;align-items:center;gap:4px;color:var(--muted);font-weight:500;white-space:nowrap;font-family:"Poppins",sans-serif}
.brand .dot{border-radius:50%;background:var(--blue);flex:none}

.cover-brand{left:17px;top:40px;font-size:15px}
.cover-brand .dot{width:18px;height:18px}
.cover-title{left:17px;top:104px;font-size:29px;line-height:36px;color:var(--ink);font-weight:400;letter-spacing:-.3px}
.cover-title strong{display:block;color:var(--blue);font-weight:700}
.cover-bar{left:17px;top:228px;width:61px;height:3px;background:var(--blue)}
.cover-sub{left:17px;top:252px;font-size:15.5px;line-height:23px;color:var(--ink);font-weight:300}
.cover-sub b{font-weight:700}
.cover-url{left:0;width:100%;top:377px;text-align:center;font-size:4.6px;color:var(--ink)}

.rule-head{display:flex;align-items:center;gap:6px;color:var(--blue);font-weight:700;white-space:nowrap}
.rule-head::before,.rule-head::after{content:"";flex:1;height:.5px;background:var(--rule)}

.p2 .brand-c{left:0;width:100%;top:33px;justify-content:center;font-size:9.5px}
.p2 .brand-c .dot{width:11px;height:11px}
.retainer-head{left:17px;width:280px;top:72px;font-size:11.5px}
.retainer-text{left:17px;width:280px;top:91px;font-size:5.4px;line-height:11.4px;text-align:justify}
.retainer-text .hl{color:var(--blue);font-weight:600}

.small{font-size:3.85px;line-height:5.75px;text-align:justify}
.small h4{color:var(--blue);font-weight:400;font-size:4.1px;line-height:5.8px}
.small p+h4{margin-top:4px}

.tooth-art{left:26px;top:23px;width:64px;height:97px;border-radius:6px;background:linear-gradient(160deg,#e6f4fb,#c4e5f5)}
.treat-head{left:100px;width:198px;top:13px;font-size:7.4px}
.treat-text{left:99px;width:199px;top:25px}
.benefit-head{left:17px;width:281px;top:155px;font-size:7.4px}
.benefit-text{left:17px;width:195px;top:168px}
.benefit-art{left:222px;top:165px;width:66px;height:44px;border-radius:6px;background:linear-gradient(160deg,#e6f4fb,#c4e5f5)}
.hr{height:.5px;background:var(--rule)}
.risk-rule{left:17px;width:281px;top:230px}
.risk-vrule{left:157px;top:230px;width:.5px;height:115px;background:var(--rule)}
.risk-head{left:17px;top:233px;font-size:7.4px;color:var(--blue);font-weight:700}
.risk-left{left:17px;width:136px;top:245px}
.risk-right{left:162px;width:136px;top:236px}

.cont-left{left:17px;width:136px;top:9px}
.cont-right{left:161px;width:136px;top:14px}
.p4 .small{font-size:3.7px;line-height:5.5px}
.p4 .small h4{font-size:3.9px;line-height:5.5px}
.p4 .small p+h4{margin-top:3.5px}

.kev{left:0;width:100%;top:26px;justify-content:center;font-size:12px;color:var(--muted)}
.kev .dot{width:16px;height:16px;background:#9a9a9a}
.consent-head{left:17px;width:280px;top:69px;font-size:8.6px}
.consent{left:12px;width:285px;top:86px;font-size:5.5px;color:var(--ink)}
.consent li{list-style:none;position:relative;padding-left:5px;line-height:10.7px}
.consent li::before{content:"";position:absolute;left:0;top:4.5px;width:1.6px;height:1.6px;border-radius:50%;background:var(--blue)}
.consent li.blank::before{display:none}
.dots{border-bottom:.6px dotted #555;height:10px;margin-left:5px}
.field{display:flex;gap:2px}
.field span.fill{flex:1;border-bottom:.6px dotted #555;margin-bottom:3px}

.pay-title{left:17px;top:15px;font-size:10.5px;font-weight:700;color:var(--ink)}
.pay-brand{left:232px;top:17px;font-size:7px}
.pay-brand .dot{width:9px;height:9px}
.pay-body{font-size:5px;line-height:9.5px;color:var(--ink)}
.pay-bullet{font-size:7.6px;font-weight:700;color:var(--blue);left:11px}
.pay-bullet::before{content:"•";margin-right:3px}
.check{width:9px;height:9px;border:.8px solid var(--ink);border-radius:1px}
.opt{font-size:5.2px;font-weight:500;color:var(--ink)}
.line-row{font-size:4.6px;color:var(--ink);display:flex;justify-content:space-between}
.line-row b{font-weight:700}
.addr-row{position:absolute;left:17px;width:281px;top:339px;display:flex;justify-content:space-around;font-size:3.5px;color:var(--ink)}
.addr-row span{display:flex;align-items:center;gap:2px}

.footer{position:absolute;left:17px;width:281px;top:352px;border-top:.5px solid var(--rule);display:flex;padding-top:4px;color:var(--ink)}
.footer .col{padding-right:6px}
.footer .col+.col{border-left:.5px solid var(--rule);padding-left:6px}
.footer .c1{width:88px}.footer .c2{width:92px}.footer .c3{flex:1}
.footer h5{font-size:3.9px;font-weight:500;margin-bottom:2px}
.footer .item{display:flex;gap:2.5px;font-size:2.8px;line-height:3.7px;margin-bottom:2px;align-items:flex-start}
.footer .item b{font-weight:600;display:block}
.ico{width:5px;height:5px;flex:none;fill:none;stroke:var(--blue);stroke-width:1}
.bank{display:grid;grid-template-columns:30px 1fr;font-size:3px;line-height:5.6px}
.bank .k{color:var(--blue);font-weight:600}
</style>
</head>
<body>

<section class="page p1">
  <div class="abs brand cover-brand"><span class="dot"></span>lumen orthodontics</div>
  <h1 class="abs cover-title">ORTHODONTIC<strong>TREATMENT</strong>CONSENT</h1>
  <div class="abs cover-bar"></div>
  <p class="abs cover-sub">Patient Information<br>and <b>Treatment</b><br><b>Agreement</b></p>
  <p class="abs cover-url">lumen-ortho.example</p>
</section>

<section class="page p2">
  <div class="abs brand brand-c"><span class="dot"></span>lumen orthodontics</div>
  <h2 class="abs rule-head retainer-head">Our retainer policy</h2>
  <p class="abs retainer-text">Wearing your retainers is the most important part of your orthodontic journey. Teeth shifting is a part of the natural ageing process just like getting wrinkles, so lifetime maintenance is crucial. Healthy teeth are not meant to be glued together, they are individual units and function independently. This is normally only done for areas of weak bone and gum or damaged teeth. For this reason <span class="hl">WE DO NOT ENCOURAGE THE USE OF ‘BONDED’ OR ‘PERMANENT’ RETAINERS.</span> Instead we advocate responsible use of removable retainers to maintain your smile. Permanent or bonded retainers are not actually permanent and can cause other unexpected problems after treatment is completed, such as difficulty to clean around those teeth which can cause plaque trapping and lead to localised gum and bone loss. They are subject to breaking frequently, which is the reason that when bonded retainers are placed, it is recommended that you still wear a removable retainer over them anyway. Bonded retainers only hold the front few teeth, whereas your orthodontic treatment involved improvements of ALL your teeth. Thus, holding the front teeth only gives the back teeth a chance to move out of alignment. The retainers we provide at Lumen Orthodontics, are only worn at night and will hold ALL your teeth where they are at the end of your orthodontic treatment. Even excellent retainer wear will not guarantee that the teeth will stay exactly the same forever, due to the natural ageing and bone changing processes. Minor alignment adjustments may be made to your retainers in the future to ensure that you remain happy with your smile. After 2 years of retainer reviews, further follow up care may be charged at the current office visit rate. Lost or broken retainers will incur a fee for replacement or repair.</p>
  <footer class="footer">
    <div class="col c1"><h5>Locations:</h5>
      <div class="item"><svg class="ico" viewBox="0 0 10 10"><path d="M5 9.3C3 7 2 5.6 2 4a3 3 0 0 1 6 0c0 1.6-1 3-3 5.3z"/><circle cx="5" cy="4" r="1"/></svg><span><b>Eastvale</b>14 Harbour Rd, Eastvale VIC 3000</span></div>
      <div class="item"><svg class="ico" viewBox="0 0 10 10"><path d="M5 9.3C3 7 2 5.6 2 4a3 3 0 0 1 6 0c0 1.6-1 3-3 5.3z"/><circle cx="5" cy="4" r="1"/></svg><span><b>Northgate</b>8 Linden Rise, Northgate VIC 3001</span></div>
      <div class="item"><svg class="ico" viewBox="0 0 10 10"><path d="M5 9.3C3 7 2 5.6 2 4a3 3 0 0 1 6 0c0 1.6-1 3-3 5.3z"/><circle cx="5" cy="4" r="1"/></svg><span><b>Hillcrest</b>52 Maple St, Hillcrest VIC 3002</span></div>
    </div>
    <div class="col c2"><h5>Information:</h5>
      <div class="item"><svg class="ico" viewBox="0 0 10 10"><path d="M2 1.5h2l1 2-1.2 1a5 5 0 0 0 2.7 2.7l1-1.2 2 1v2C5 9 1 5 2 1.5z"/></svg><span>03 5550 1234</span></div>
      <div class="item"><svg class="ico" viewBox="0 0 10 10"><rect x="2" y="4" width="6" height="4"/><path d="M3 4V1.5h4V4"/></svg><span>03 5550 5678</span></div>
      <div class="item"><svg class="ico" viewBox="0 0 10 10"><rect x="1" y="2.5" width="8" height="5"/><path d="M1 2.5l4 3 4-3"/></svg><span>hello@lumen-ortho.example</span></div>
      <div class="item"><svg class="ico" viewBox="0 0 10 10"><circle cx="5" cy="5" r="3.8"/><path d="M1.2 5h7.6M5 1.2c-2 2.5-2 5 0 7.6M5 1.2c2 2.5 2 5 0 7.6"/></svg><span>lumen-ortho.example</span></div>
    </div>
    <div class="col c3"><h5>Registered Specialist Orthodontists:</h5>
      <div class="item"><svg class="ico" viewBox="0 0 10 10"><path d="M2 2c1-1 2.5-.5 3 0 .5-.5 2-1 3 0s.3 3-.3 4.5L7 9 5.8 6H4.2L3 9 2.3 6.5C1.7 5 1 3 2 2z"/></svg><span><b>Dr Hannah Reyes</b>MDSc, Grad Dip Clin Dent, BDSc(Hons)</span></div>
      <div class="item"><svg class="ico" viewBox="0 0 10 10"><path d="M2 2c1-1 2.5-.5 3 0 .5-.5 2-1 3 0s.3 3-.3 4.5L7 9 5.8 6H4.2L3 9 2.3 6.5C1.7 5 1 3 2 2z"/></svg><span><b>Dr Tom Aldridge</b>MDSc, Grad Dip Clin Dent, MOrth, BDSc</span></div>
      <div class="item"><svg class="ico" viewBox="0 0 10 10"><path d="M2 2c1-1 2.5-.5 3 0 .5-.5 2-1 3 0s.3 3-.3 4.5L7 9 5.8 6H4.2L3 9 2.3 6.5C1.7 5 1 3 2 2z"/></svg><span><b>Dr Mina Park</b>DCD, MOrth, MRACDS (Orth), BDSc (Hons)</span></div>
    </div>
  </footer>
</section>

<section class="page p3">
  <div class="abs tooth-art" role="img" aria-label="Line illustration of a tooth being cleaned by a dental tool"></div>
  <h2 class="abs rule-head treat-head">ORTHODONTIC TREATMENT</h2>
  <p class="abs small treat-text">Orthodontic treatment promotes a healthy smile, healthier teeth and gums and a better bite for normal chewing. Orthodontic treatment depends for much of its success on the understanding and co-operation of the patient. This form covers the usual material risks associated with orthodontic treatment. Other factors may also be described by your orthodontist. You may ask your orthodontist to explain anything you do not understand. While recognising the benefits of healthy teeth and a pleasing smile, you should also be aware that orthodontic treatment has limitations and potential risks and there may be alternative treatment options. You should clarify what is expected of you as a patient, or as the parent of a young patient, to achieve excellent results. Keep in mind that with orthodontic treatment, like other healing arts, results cannot be guaranteed. The unknown factor in any orthodontic correction is the response of the patient to the orthodontic treatment. Should you have any questions, please ask. The benefits of healthy teeth and a pleasing smile come with limitations and potential risks and there may be alternative treatment options. You should clarify what is expected of you as a patient, or as the parent of a young patient, to achieve excellent results. Keep in mind that with orthodontic treatment, like other healing arts, results cannot be guaranteed. The unknown factor in any orthodontic correction is the response of the patient to the orthodontic treatment. Should you have any questions, please ask.</p>
  <h3 class="abs rule-head benefit-head">BENEFITS</h3>
  <p class="abs small benefit-text">Orthodontics plays an important role in improving overall oral health and achieving balance and harmony between the face and teeth for a healthy smile, which may enhance one’s self esteem. Properly aligned teeth and a correct bite promote optimal chewing function and make brushing easier, potentially reducing risk of decay and gum disease. Correctly aligned teeth are less likely to experience abnormal wear. Because of the individual conditions present and the limitations of treatment imposed by nature, each specific benefit may not be attainable for every patient.</p>
  <div class="abs benefit-art" role="img" aria-label="Line illustration of a hand holding a row of healthy teeth"></div>
  <div class="abs hr risk-rule"></div>
  <div class="abs risk-vrule"></div>
  <h3 class="abs risk-head">RISKS</h3>
  <div class="abs small risk-left">
    <p>All forms of medical and dental treatment, including orthodontics, have some risks and limitations. Fortunately, in orthodontics complications are rare and are usually of a minor consequence if they do occur. Nevertheless, all risks should be considered when making the decision to undergo orthodontic treatment. The principal risks in orthodontic treatment are:</p>
    <h4 style="margin-top:10px">1. Oral Hygiene</h4>
    <p>Orthodontic appliances do not cause tooth decay. Gum disease, tooth decay and permanent markings (decalcification) on the teeth can occur if orthodontic patients eat sugary food and drinks or do not brush their teeth frequently or properly. These same problems can occur without orthodontic treatment, but the risk is greater to an individual wearing orthodontic appliances. It is imperative that extra care be taken with oral hygiene during orthodontic treatment.</p>
  </div>
  <div class="abs small risk-right">
    <h4>2 Enamel or Restoration Damage</h4>
    <p>Minor tooth surface cracks (known as enamel crazing) or, in rare cases, enamel fractures may occur during orthodontics. Damage to the enamel of a tooth or to a restoration (crown, bonding, veneer, etc.) is possible when orthodontic appliances are removed. If the enamel is weaker, the depth of this damage can be deeper and may need restoration. This problem may be more likely when aesthetic (clear or tooth coloured) appliances have been selected. Healthy enamel is less likely to have damage. Your dentist can help if needed.</p>
    <h4 style="margin-top:10px">3 Speech</h4>
    <p>Speech can be affected for a short time after appliances are placed. This is more common when there is less room for the tongue. Speech may improve with practice.</p>
  </div>
  <footer class="footer">
    <div class="col c1"><h5>Locations:</h5>
      <div class="item"><svg class="ico" viewBox="0 0 10 10"><path d="M5 9.3C3 7 2 5.6 2 4a3 3 0 0 1 6 0c0 1.6-1 3-3 5.3z"/><circle cx="5" cy="4" r="1"/></svg><span><b>Eastvale</b>14 Harbour Rd, Eastvale VIC 3000</span></div>
      <div class="item"><svg class="ico" viewBox="0 0 10 10"><path d="M5 9.3C3 7 2 5.6 2 4a3 3 0 0 1 6 0c0 1.6-1 3-3 5.3z"/><circle cx="5" cy="4" r="1"/></svg><span><b>Northgate</b>8 Linden Rise, Northgate VIC 3001</span></div>
      <div class="item"><svg class="ico" viewBox="0 0 10 10"><path d="M5 9.3C3 7 2 5.6 2 4a3 3 0 0 1 6 0c0 1.6-1 3-3 5.3z"/><circle cx="5" cy="4" r="1"/></svg><span><b>Hillcrest</b>52 Maple St, Hillcrest VIC 3002</span></div>
    </div>
    <div class="col c2"><h5>Information:</h5>
      <div class="item"><svg class="ico" viewBox="0 0 10 10"><path d="M2 1.5h2l1 2-1.2 1a5 5 0 0 0 2.7 2.7l1-1.2 2 1v2C5 9 1 5 2 1.5z"/></svg><span>03 5550 1234</span></div>
      <div class="item"><svg class="ico" viewBox="0 0 10 10"><rect x="2" y="4" width="6" height="4"/><path d="M3 4V1.5h4V4"/></svg><span>03 5550 5678</span></div>
      <div class="item"><svg class="ico" viewBox="0 0 10 10"><rect x="1" y="2.5" width="8" height="5"/><path d="M1 2.5l4 3 4-3"/></svg><span>hello@lumen-ortho.example</span></div>
      <div class="item"><svg class="ico" viewBox="0 0 10 10"><circle cx="5" cy="5" r="3.8"/><path d="M1.2 5h7.6M5 1.2c-2 2.5-2 5 0 7.6M5 1.2c2 2.5 2 5 0 7.6"/></svg><span>lumen-ortho.example</span></div>
    </div>
    <div class="col c3"><h5>Registered Specialist Orthodontists:</h5>
      <div class="item"><svg class="ico" viewBox="0 0 10 10"><path d="M2 2c1-1 2.5-.5 3 0 .5-.5 2-1 3 0s.3 3-.3 4.5L7 9 5.8 6H4.2L3 9 2.3 6.5C1.7 5 1 3 2 2z"/></svg><span><b>Dr Hannah Reyes</b>MDSc, Grad Dip Clin Dent, BDSc(Hons)</span></div>
      <div class="item"><svg class="ico" viewBox="0 0 10 10"><path d="M2 2c1-1 2.5-.5 3 0 .5-.5 2-1 3 0s.3 3-.3 4.5L7 9 5.8 6H4.2L3 9 2.3 6.5C1.7 5 1 3 2 2z"/></svg><span><b>Dr Tom Aldridge</b>MDSc, Grad Dip Clin Dent, MOrth, BDSc</span></div>
      <div class="item"><svg class="ico" viewBox="0 0 10 10"><path d="M2 2c1-1 2.5-.5 3 0 .5-.5 2-1 3 0s.3 3-.3 4.5L7 9 5.8 6H4.2L3 9 2.3 6.5C1.7 5 1 3 2 2z"/></svg><span><b>Dr Mina Park</b>DCD, MOrth, MRACDS (Orth), BDSc (Hons)</span></div>
    </div>
  </footer>
</section>

<section class="page p4">
  <div class="abs small cont-left">
    <h4>4 Relapse</h4>
    <p>Teeth may tend to change their positions after treatment. The long term, faithful wearing of retainers should reduce this tendency. Teeth can, however, move any time, whether or not they have had orthodontic treatment. This is especially true during the late teen period when active growth of the face is coming to an end. The most vulnerable teeth are those at the front. Throughout life the bite can change adversely from various causes such as eruption of wisdom teeth, growth or maturational changes, mouth breathing, playing of musical instruments and other oral habits. Very occasionally tooth movements will be severe enough to merit a further course of treatment to ensure a satisfactory result.</p>
    <h4>5 Periodontal Health</h4>
    <p>The health of the bone and gums which support the teeth may be affected by orthodontic tooth movement if periodontal disease already exists, and in some rare cases where periodontal disease does not appear to exist. Orthodontic treatment may lessen the risk of tooth loss or gum infection due to misalignment of the teeth or jaws. Inflammation of the gums and loss of supporting bone can occur if bacterial plaque is not removed daily with good oral hygiene.</p>
    <h4>6 Root Shortening</h4>
    <p>In some patients, the length of the roots of the teeth may be shortened during orthodontic treatment. It is nearly impossible to predict patient susceptibility to root shortening. Usually, this shortening does not have significant consequences, but on very rare occasions it may compromise the longevity of the teeth involved.</p>
    <h4>7 Jaw Joints</h4>
    <p>Occasionally patients may suffer pain or dysfunction in the jaw joints (TMJ). This may present as joint pain, headaches, or ear problems. These problems may occur with or without orthodontic treatment. Any of the above noted symptoms should be reported to the orthodontist. Some patients are susceptible to TMJ problems, and some are not. Numerous studies have shown that the movement of the teeth during orthodontic treatment is unrelated to the onset of TMJ problems. Just as for painful conditions in other joints, discomfort in TMJ can last from a few days to several weeks or longer.</p>
    <h4>8 Tooth Vitality</h4>
    <p>Sometimes a tooth may have been traumatised by a previous accident or a tooth may be decayed or have fillings which can cause damage to the nerve of the tooth. Orthodontic tooth movement may aggravate this condition and in rare instances may lead to loss of tooth vitality and discolouration of the tooth requiring root canal treatment and other dental treatment to restore the colour of the tooth.</p>
    <h4>9 Loose appliances and discomfort</h4>
    <p>The gums, cheeks or lips may be scratched or irritated by newly placed appliances or by loose or broken appliances or by trauma to the mouth. You will be given instructions on minimising these effects. Very rarely, loose orthodontic appliances may be accidentally swallowed or aspirated.</p>
  </div>
  <div class="abs small cont-right">
    <p>You should inform your orthodontist of any unusual symptoms, or broken or loose appliances, as soon as they are noted. Usual post-adjustment tenderness or sensitivity of 24–48 hours should be expected, although this can vary with each patient and the procedure performed.</p>
    <h4>10 Atypical Growth</h4>
    <p>Insufficient excessive or asymmetrical changes in the growth of the jaws may limit the orthodontist’s ability to achieve the desired result. If growth becomes disproportionate during orthodontic management the treatment may be prolonged. Growth changes that occur after orthodontic treatment may alter the quality of treatment results and may require further orthodontic treatment. In some cases of atypical growth, the bite may change so much that oral surgery is required to achieve the best possible result.</p>
    <h4>11 Headgear</h4>
    <p>If improperly handled, headgear may cause facial injury. Patients are warned not to wear the appliance during times of boisterous or competitive activity.</p>
    <h4>12 Treatment Time</h4>
    <p>The duration of orthodontic treatment can vary depending on factors such as the complexity of the case and patient compliance. Total treatment time may exceed the estimate and delays are more likely with lost or broken appliances, missed appointments, poor cooperation, or unexpected complications.</p>
    <h4>13 Co-operation</h4>
    <p>Co-operation throughout treatment is your best guarantee of achieving a pleasing smile and a good bite. It is vital to follow your orthodontist’s instructions on all aspects of treatment (i.e. wearing elastics, aligners and retainers for the prescribed amount of time). Without your co-operation, treatment may not be as successful. Your orthodontist may need to consider a change in treatment plan or, in rare situations, stop treatment or accept less than ideal results. Best results will occur when you work well with your orthodontist.</p>
    <h4>14 Complementary aesthetic dentistry</h4>
    <p>In some situations, achieving the desired aesthetic outcome may require additional dental procedures, such as cosmetic bonding, crowns, or periodontal therapy, to address specific issues not corrected by orthodontic treatment alone.</p>
    <h4>15 General Health</h4>
    <p>General medical problems can affect orthodontic treatment. You should keep your orthodontist informed of any changes to your medical health.</p>
    <h4>16 Specific Risks</h4>
    <p>Your orthodontist will discuss your case with you in detail and discuss specific risks.</p>
  </div>
  <footer class="footer">
    <div class="col c1"><h5>Locations:</h5>
      <div class="item"><svg class="ico" viewBox="0 0 10 10"><path d="M5 9.3C3 7 2 5.6 2 4a3 3 0 0 1 6 0c0 1.6-1 3-3 5.3z"/><circle cx="5" cy="4" r="1"/></svg><span><b>Eastvale</b>14 Harbour Rd, Eastvale VIC 3000</span></div>
      <div class="item"><svg class="ico" viewBox="0 0 10 10"><path d="M5 9.3C3 7 2 5.6 2 4a3 3 0 0 1 6 0c0 1.6-1 3-3 5.3z"/><circle cx="5" cy="4" r="1"/></svg><span><b>Northgate</b>8 Linden Rise, Northgate VIC 3001</span></div>
      <div class="item"><svg class="ico" viewBox="0 0 10 10"><path d="M5 9.3C3 7 2 5.6 2 4a3 3 0 0 1 6 0c0 1.6-1 3-3 5.3z"/><circle cx="5" cy="4" r="1"/></svg><span><b>Hillcrest</b>52 Maple St, Hillcrest VIC 3002</span></div>
    </div>
    <div class="col c2"><h5>Information:</h5>
      <div class="item"><svg class="ico" viewBox="0 0 10 10"><path d="M2 1.5h2l1 2-1.2 1a5 5 0 0 0 2.7 2.7l1-1.2 2 1v2C5 9 1 5 2 1.5z"/></svg><span>03 5550 1234</span></div>
      <div class="item"><svg class="ico" viewBox="0 0 10 10"><rect x="2" y="4" width="6" height="4"/><path d="M3 4V1.5h4V4"/></svg><span>03 5550 5678</span></div>
      <div class="item"><svg class="ico" viewBox="0 0 10 10"><rect x="1" y="2.5" width="8" height="5"/><path d="M1 2.5l4 3 4-3"/></svg><span>hello@lumen-ortho.example</span></div>
      <div class="item"><svg class="ico" viewBox="0 0 10 10"><circle cx="5" cy="5" r="3.8"/><path d="M1.2 5h7.6M5 1.2c-2 2.5-2 5 0 7.6M5 1.2c2 2.5 2 5 0 7.6"/></svg><span>lumen-ortho.example</span></div>
    </div>
    <div class="col c3"><h5>Registered Specialist Orthodontists:</h5>
      <div class="item"><svg class="ico" viewBox="0 0 10 10"><path d="M2 2c1-1 2.5-.5 3 0 .5-.5 2-1 3 0s.3 3-.3 4.5L7 9 5.8 6H4.2L3 9 2.3 6.5C1.7 5 1 3 2 2z"/></svg><span><b>Dr Hannah Reyes</b>MDSc, Grad Dip Clin Dent, BDSc(Hons)</span></div>
      <div class="item"><svg class="ico" viewBox="0 0 10 10"><path d="M2 2c1-1 2.5-.5 3 0 .5-.5 2-1 3 0s.3 3-.3 4.5L7 9 5.8 6H4.2L3 9 2.3 6.5C1.7 5 1 3 2 2z"/></svg><span><b>Dr Tom Aldridge</b>MDSc, Grad Dip Clin Dent, MOrth, BDSc</span></div>
      <div class="item"><svg class="ico" viewBox="0 0 10 10"><path d="M2 2c1-1 2.5-.5 3 0 .5-.5 2-1 3 0s.3 3-.3 4.5L7 9 5.8 6H4.2L3 9 2.3 6.5C1.7 5 1 3 2 2z"/></svg><span><b>Dr Mina Park</b>DCD, MOrth, MRACDS (Orth), BDSc (Hons)</span></div>
    </div>
  </footer>
</section>

<section class="page p5">
  <div class="abs brand kev"><span class="dot"></span>KEV</div>
  <h2 class="abs rule-head consent-head">CONSENT TO TREATMENT</h2>
  <ul class="abs consent">
    <li>I hereby authorize:</li>
    <li class="blank" style="padding:0"><div class="dots" style="margin-bottom:8px"></div></li>
    <li style="margin-top:3px">to carry out orthodontic treatment and any other related procedures deemed necessary including radiographs, for the welfare and treatment of:</li>
    <li class="blank" style="padding:0"><div class="dots" style="margin-bottom:8px"></div></li>
    <li style="margin-top:3px">I confirm that the risks attaching to the proposed treatment have been explained to me by my practitioner and that I fully understand those risks and have determined to proceed with treatment. Signature of patient (or parent/guardian for patients under the age of 18 years):</li>
    <li style="margin-top:9px" class="field">Signature: <span class="fill"></span></li>
    <li style="margin-top:10.5px" class="field">Name: <span class="fill"></span></li>
    <li style="margin-top:10.5px" class="field">Relationship to patient: <span class="fill"></span></li>
    <li style="margin-top:10.5px" class="field">Date: ............ / ..................... / <span class="fill"></span></li>
    <li style="margin-top:10.5px" class="field">Signature of Orthodontist: <span class="fill"></span></li>
  </ul>
  <footer class="footer">
    <div class="col c1"><h5>Locations:</h5>
      <div class="item"><svg class="ico" viewBox="0 0 10 10"><path d="M5 9.3C3 7 2 5.6 2 4a3 3 0 0 1 6 0c0 1.6-1 3-3 5.3z"/><circle cx="5" cy="4" r="1"/></svg><span><b>Eastvale</b>14 Harbour Rd, Eastvale VIC 3000</span></div>
      <div class="item"><svg class="ico" viewBox="0 0 10 10"><path d="M5 9.3C3 7 2 5.6 2 4a3 3 0 0 1 6 0c0 1.6-1 3-3 5.3z"/><circle cx="5" cy="4" r="1"/></svg><span><b>Northgate</b>8 Linden Rise, Northgate VIC 3001</span></div>
      <div class="item"><svg class="ico" viewBox="0 0 10 10"><path d="M5 9.3C3 7 2 5.6 2 4a3 3 0 0 1 6 0c0 1.6-1 3-3 5.3z"/><circle cx="5" cy="4" r="1"/></svg><span><b>Hillcrest</b>52 Maple St, Hillcrest VIC 3002</span></div>
    </div>
    <div class="col c2"><h5>Information:</h5>
      <div class="item"><svg class="ico" viewBox="0 0 10 10"><path d="M2 1.5h2l1 2-1.2 1a5 5 0 0 0 2.7 2.7l1-1.2 2 1v2C5 9 1 5 2 1.5z"/></svg><span>03 5550 1234</span></div>
      <div class="item"><svg class="ico" viewBox="0 0 10 10"><rect x="2" y="4" width="6" height="4"/><path d="M3 4V1.5h4V4"/></svg><span>03 5550 5678</span></div>
      <div class="item"><svg class="ico" viewBox="0 0 10 10"><rect x="1" y="2.5" width="8" height="5"/><path d="M1 2.5l4 3 4-3"/></svg><span>hello@lumen-ortho.example</span></div>
      <div class="item"><svg class="ico" viewBox="0 0 10 10"><circle cx="5" cy="5" r="3.8"/><path d="M1.2 5h7.6M5 1.2c-2 2.5-2 5 0 7.6M5 1.2c2 2.5 2 5 0 7.6"/></svg><span>lumen-ortho.example</span></div>
    </div>
    <div class="col c3"><h5>Registered Specialist Orthodontists:</h5>
      <div class="item"><svg class="ico" viewBox="0 0 10 10"><path d="M2 2c1-1 2.5-.5 3 0 .5-.5 2-1 3 0s.3 3-.3 4.5L7 9 5.8 6H4.2L3 9 2.3 6.5C1.7 5 1 3 2 2z"/></svg><span><b>Dr Hannah Reyes</b>MDSc, Grad Dip Clin Dent, BDSc(Hons)</span></div>
      <div class="item"><svg class="ico" viewBox="0 0 10 10"><path d="M2 2c1-1 2.5-.5 3 0 .5-.5 2-1 3 0s.3 3-.3 4.5L7 9 5.8 6H4.2L3 9 2.3 6.5C1.7 5 1 3 2 2z"/></svg><span><b>Dr Tom Aldridge</b>MDSc, Grad Dip Clin Dent, MOrth, BDSc</span></div>
      <div class="item"><svg class="ico" viewBox="0 0 10 10"><path d="M2 2c1-1 2.5-.5 3 0 .5-.5 2-1 3 0s.3 3-.3 4.5L7 9 5.8 6H4.2L3 9 2.3 6.5C1.7 5 1 3 2 2z"/></svg><span><b>Dr Mina Park</b>DCD, MOrth, MRACDS (Orth), BDSc (Hons)</span></div>
    </div>
  </footer>
</section>

<section class="page p6">
  <h2 class="abs pay-title">Payment Option Selection</h2>
  <div class="abs brand pay-brand"><span class="dot"></span>lumen orthodontics</div>
  <p class="abs pay-body" style="left:17px;top:35px;font-weight:600">Thank you for choosing Lumen Orthodontics.</p>
  <p class="abs pay-body" style="left:17px;width:281px;top:46px">To assist with managing your treatment fees, please select your preferred payment method below. If you would prefer to pay at each scheduled appointment, please advise our reception team. Please note that appointments are generally scheduled every 6–8 weeks.</p>
  <div class="abs hr" style="left:17px;width:281px;top:80px"></div>
  <h3 class="abs pay-bullet" style="top:85px">Please select one option:</h3>

  <div class="abs check" style="left:20px;top:103px"></div>
  <p class="abs opt" style="left:35px;top:103px">Credit Card Direct Debit</p>
  <svg class="abs" style="left:147px;top:104px" width="28" height="20" viewBox="0 0 28 20" fill="none" stroke="#1a9ad6" stroke-width=".8"><rect x="1" y="1" width="22" height="14" rx="1.5"/><path d="M1 5h22M4 10h8"/><circle cx="22" cy="14" r="4.5" fill="#fff"/><path d="M20 14h4M22.5 12.5 24 14l-1.5 1.5"/></svg>
  <p class="abs pay-body" style="left:17px;top:115px">I would like to pay via credit card direct debit.</p>
  <p class="abs pay-body" style="left:17px;width:281px;top:129px;line-height:7.3px">I understand that Lumen Orthodontics will send me a secure PayLink payment link to enter my credit card details. The card provided will be securely stored and used as my nominated payment method for future scheduled payments relating to my treatment plan.</p>
  <div class="abs hr" style="left:17px;width:268px;top:161px"></div>

  <div class="abs check" style="left:20px;top:169px"></div>
  <p class="abs opt" style="left:35px;top:169px">Monthly Direct Bank Transfer</p>
  <svg class="abs" style="left:147px;top:168px" width="22" height="21" viewBox="0 0 22 21" fill="none" stroke="#1a9ad6" stroke-width=".8"><rect x="1" y="3" width="20" height="17" rx="2"/><path d="M6 1v4M16 1v4M5 10h11l-2-2M16 14H5l2 2"/></svg>
  <p class="abs pay-body" style="left:17px;top:182px">I would like to pay via monthly direct bank transfer.</p>
  <p class="abs pay-body" style="left:17px;width:281px;top:197px;line-height:7.3px">I understand that I am responsible for ensuring monthly payments are made on time in accordance with my agreed payment arrangement.</p>
  <div class="abs hr" style="left:17px;width:281px;top:220px"></div>

  <h3 class="abs pay-bullet" style="top:227px">Important</h3>
  <p class="abs pay-body" style="left:17px;width:281px;top:240px;line-height:7.3px">When making direct transfer payments, please use the <b>patient’s full name</b> as the payment reference (for example: Jane Citizen), rather than the account holder’s name. This ensures payments are correctly allocated to your treatment account.</p>
  <h3 class="abs pay-bullet" style="top:266px">Patient Declaration</h3>
  <p class="abs pay-body" style="left:16px;top:279px;font-weight:600">I hereby authorise Lumen Orthodontics</p>
  <div class="abs line-row" style="left:17px;width:281px;top:314px"><b>Patient name: ...............................</b><b>Signature of Parent: ...........................</b><b>Date: .........../.........../.............</b></div>
  <div class="abs hr" style="left:17px;width:281px;top:335px"></div>
  <div class="addr-row">
    <span><svg class="ico" viewBox="0 0 10 10"><path d="M5 9.3C3 7 2 5.6 2 4a3 3 0 0 1 6 0c0 1.6-1 3-3 5.3z"/><circle cx="5" cy="4" r="1"/></svg>14 Harbour Rd, Eastvale VIC 3000</span>
    <span><svg class="ico" viewBox="0 0 10 10"><path d="M5 9.3C3 7 2 5.6 2 4a3 3 0 0 1 6 0c0 1.6-1 3-3 5.3z"/><circle cx="5" cy="4" r="1"/></svg>8 Linden Rise, Northgate VIC 3001</span>
    <span><svg class="ico" viewBox="0 0 10 10"><path d="M5 9.3C3 7 2 5.6 2 4a3 3 0 0 1 6 0c0 1.6-1 3-3 5.3z"/><circle cx="5" cy="4" r="1"/></svg>52 Maple St, Hillcrest VIC 3002</span>
  </div>
  <footer class="footer">
    <div class="col c1"><h5>Our bank account details:</h5>
      <div class="bank">
        <span class="k">Account Name</span><span>: Lumen Orthodontics</span>
        <span class="k">Bank</span><span>: Harbour Bank</span>
        <span class="k">BSB</span><span>: 000 111</span>
        <span class="k">Account Number</span><span>: 12345678</span>
      </div>
    </div>
    <div class="col c2"><h5>Information:</h5>
      <div class="item"><svg class="ico" viewBox="0 0 10 10"><path d="M2 1.5h2l1 2-1.2 1a5 5 0 0 0 2.7 2.7l1-1.2 2 1v2C5 9 1 5 2 1.5z"/></svg><span>03 5550 1234</span></div>
      <div class="item"><svg class="ico" viewBox="0 0 10 10"><rect x="2" y="4" width="6" height="4"/><path d="M3 4V1.5h4V4"/></svg><span>03 5550 5678</span></div>
      <div class="item"><svg class="ico" viewBox="0 0 10 10"><rect x="1" y="2.5" width="8" height="5"/><path d="M1 2.5l4 3 4-3"/></svg><span>hello@lumen-ortho.example</span></div>
      <div class="item"><svg class="ico" viewBox="0 0 10 10"><circle cx="5" cy="5" r="3.8"/><path d="M1.2 5h7.6M5 1.2c-2 2.5-2 5 0 7.6M5 1.2c2 2.5 2 5 0 7.6"/></svg><span>lumen-ortho.example</span></div>
    </div>
    <div class="col c3"><h5>Registered Specialist Orthodontists:</h5>
      <div class="item"><svg class="ico" viewBox="0 0 10 10"><path d="M2 2c1-1 2.5-.5 3 0 .5-.5 2-1 3 0s.3 3-.3 4.5L7 9 5.8 6H4.2L3 9 2.3 6.5C1.7 5 1 3 2 2z"/></svg><span><b>Dr Hannah Reyes</b>MDSc, Grad Dip Clin Dent, BDSc(Hons)</span></div>
      <div class="item"><svg class="ico" viewBox="0 0 10 10"><path d="M2 2c1-1 2.5-.5 3 0 .5-.5 2-1 3 0s.3 3-.3 4.5L7 9 5.8 6H4.2L3 9 2.3 6.5C1.7 5 1 3 2 2z"/></svg><span><b>Dr Tom Aldridge</b>MDSc, Grad Dip Clin Dent, MOrth, BDSc</span></div>
      <div class="item"><svg class="ico" viewBox="0 0 10 10"><path d="M2 2c1-1 2.5-.5 3 0 .5-.5 2-1 3 0s.3 3-.3 4.5L7 9 5.8 6H4.2L3 9 2.3 6.5C1.7 5 1 3 2 2z"/></svg><span><b>Dr Mina Park</b>DCD, MOrth, MRACDS (Orth), BDSc (Hons)</span></div>
    </div>
  </footer>
</section>

</body>
</html>
```